Business Card for Professional Photographer

I'm looking for an eye catching modern clean design that compliments my logo/ website fonts & colours.
I specialise in architecture, corporate & commercial photography so I'm marketing to professional clients rather than portrait / wedding clients.

I would prefer to not have a solid black design.

My logo brand guide is as follows :

Main front font. : Reislust
Main font colour : #fff
Slogan front font : Ubuntu Bold
Monogram front font : Venti Medium
Container colour : #fff

I need print ready files in pdf .png & .eps formats.

Included in the files below are some screen grabs as reference to font & colours etc.

```html
<!DOCTYPE html>
<html lang="en">
<head>
<meta charset="utf-8">
<title>Northlight Studio – Business Card</title>
<link href="https://fonts.googleapis.com/css2?family=Ubuntu:wght@300;400;700&family=Roboto:wght@400&family=Saira+Semi+Condensed:wght@700&display=swap" rel="stylesheet">
<style>
  :root{
    --bg:#4a4a4c;
    --card-dark:#1c1c1f;
    --gold:#c9a24a;
    --gold-light:#f3e29c;
    --gold-deep:#a8801f;
    --text-light:#ffffff;
    --text-dark:#1a1a1a;
  }
  *{margin:0;padding:0;box-sizing:border-box}
  html,body{width:799px;height:1200px;overflow:hidden}
  body{background:var(--bg);position:relative;font-family:"Ubuntu",sans-serif}
  .card{position:absolute;left:60px;width:680px;height:390px;overflow:hidden;box-shadow:0 12px 30px rgba(0,0,0,.45)}
  .card--front{top:110px;background:var(--card-dark)}
  .card--back{top:700px;background:var(--card-dark)}

  .photo-grid{position:absolute;inset:0;display:grid;grid-template-columns:1fr 1fr 1.2fr;grid-template-rows:1fr 1fr;gap:3px;background:#111}
  .photo-grid div{background:linear-gradient(135deg,#2b2c31,#1a1b1f)}
  .photo-grid div:nth-child(2){background:linear-gradient(160deg,#33302b,#1d1c1a)}
  .photo-grid div:nth-child(3){background:linear-gradient(200deg,#2a2f36,#17191d)}
  .photo-grid div:nth-child(4){background:linear-gradient(120deg,#1f2a33,#141619)}
  .photo-grid div:nth-child(5){background:linear-gradient(170deg,#302b26,#191715)}
  .photo-grid div:nth-child(6){background:linear-gradient(150deg,#2e2e30,#18181a)}

  .brand{position:absolute;display:flex;align-items:center;gap:18px}
  .card--front .brand{left:60px;top:105px}
  .card--back .brand{left:60px;top:36px}
  .brand-dot{width:62px;height:62px;border-radius:50%;border:4px solid var(--gold);flex:none}
  .brand-name{font-family:"Ubuntu",sans-serif;font-weight:300;color:var(--gold);font-size:32px;letter-spacing:5px;text-transform:uppercase;line-height:1}
  .brand-slogan{font-family:"Ubuntu",sans-serif;font-weight:700;color:var(--gold-deep);font-size:13px;letter-spacing:3px;margin-top:6px}
  .website{position:absolute;left:60px;bottom:70px;color:var(--gold);font-size:20px;letter-spacing:3px;font-weight:300}

  .contact{position:absolute;left:60px;top:116px;color:var(--text-light);font-family:"Roboto",sans-serif;font-size:16px;line-height:22px;list-style:none}
  .contact li{display:flex;align-items:center;gap:10px}
  .contact svg{width:13px;height:13px;flex:none}

  .waves{position:absolute;left:0;top:0;width:680px;height:390px}
  .person{position:absolute;right:50px;bottom:34px;text-align:right;color:var(--text-dark);line-height:1.15}
  .person-name{font-family:"Saira Semi Condensed",sans-serif;font-weight:700;font-size:24px}
  .person-role{font-family:"Roboto",sans-serif;font-size:17px}
</style>
</head>
<body>

<section class="card card--front">
  <div class="photo-grid" role="img" aria-label="Darkened collage of architecture and commercial photographs">
    <div></div><div></div><div></div><div></div><div></div><div></div>
  </div>
  <div class="brand">
    <span class="brand-dot"></span>
    <div>
      <div class="brand-name">Northlight Studio</div>
      <div class="brand-slogan">Architecture Corporate Commercial</div>
    </div>
  </div>
  <p class="website">www.northlightstudio.com.au</p>
</section>

<section class="card card--back">
  <svg class="waves" viewBox="0 0 680 390" aria-hidden="true">
    <defs>
      <linearGradient id="goldFill" x1="0" y1="0" x2="1" y2="1">
        <stop offset="0" stop-color="#c9a24a"/>
        <stop offset=".5" stop-color="#f3e29c"/>
        <stop offset="1" stop-color="#f6eaa8"/>
      </linearGradient>
      <linearGradient id="goldStroke" x1="0" y1="0" x2="1" y2="0">
        <stop offset="0" stop-color="#a8801f"/>
        <stop offset=".5" stop-color="#e9cf7a"/>
        <stop offset="1" stop-color="#b8902e"/>
      </linearGradient>
    </defs>
    <path d="M0,222 C120,205 240,262 370,268 C480,273 590,250 680,220 L680,236 C590,264 480,287 370,283 C240,277 120,222 0,238 Z" fill="url(#goldStroke)"/>
    <path d="M0,248 C130,235 250,290 380,293 C500,296 600,272 680,248 L680,390 L0,390 Z" fill="url(#goldFill)"/>
    <path d="M0,258 C140,246 260,300 390,303 C510,305 600,282 680,260" fill="none" stroke="#1c1c1f" stroke-width="5"/>
  </svg>

  <div class="brand">
    <span class="brand-dot"></span>
    <div>
      <div class="brand-name">Northlight Studio</div>
      <div class="brand-slogan">Architecture Corporate Commercial</div>
    </div>
  </div>

  <ul class="contact">
    <li>48 Harbour Rd Ashford Vic 3190</li>
    <li><svg viewBox="0 0 16 16"><circle cx="8" cy="8" r="8" fill="#c9a24a"/><path d="M5 4h2l1 2-1 1c.5 1 1 1.5 2 2l1-1 2 1v2c-4 0-7-3-7-7z" fill="#1c1c1f"/></svg>0412555018</li>
    <li><svg viewBox="0 0 16 16"><rect x="1" y="3" width="14" height="10" rx="1" fill="#c9a24a"/><path d="M1 4l7 5 7-5" fill="none" stroke="#1c1c1f" stroke-width="1.3"/></svg>info@northlightstudio.com.au</li>
    <li><svg viewBox="0 0 16 16"><circle cx="8" cy="8" r="7" fill="#c9a24a"/><path d="M1 8h14M8 1c-3 3.5-3 10.5 0 14M8 1c3 3.5 3 10.5 0 14" fill="none" stroke="#1c1c1f" stroke-width="1"/></svg>www.northlightstudio.com.au</li>
  </ul>

  <div class="person">
    <div class="person-name">Daniel Marsh</div>
    <div class="person-role">Photographer</div>
  </div>
</section>

</body>
</html>
```